Brightbay Orthodontics business card design

Need a business card design that reflects our re-branding (orthodontic office - braces) and a new partnership with a pediatric dental office. We would like to include "for adults and children" on the card as well so adults know they are welcome to get their braces here as well. Office design is modern and would like business card to reflect a modern type look. Here's the text we would like to be included on the card:

Darren Wolcott, DDS, MSD
5214 West Linden Avenue, Suite 204
Ridgeford, OR 76991
555-418-2637
www.brightbayortho.example
info@brightbayortho.example

Can we add the following to the existing designs? Darren Wolcott, DDS, MSD 5214 West Linden Avenue, Suite 204 Ridgeford, OR 76991 555-418-2637

Does anyone have any more vertical designs available? Thanks!

Dental

```html
<!DOCTYPE html>
<html lang="en">
<head>
<meta charset="utf-8">
<title>Brightbay Orthodontics – Business Card</title>
<link href="https://fonts.googleapis.com/css2?family=Questrial&display=swap" rel="stylesheet">
<style>
  :root {
    --backdrop: #2e2e30;
    --card: #fbfbfb;
    --ink: #2a2a2a;
    --ink-soft: #4a4a4a;
    --band: #ececec;
    --icon-blue: #1f76bd;
    --accent-start: #1a78c2;
    --accent-end: #7cbf3a;
  }
  * { box-sizing: border-box; margin: 0; padding: 0; }
  html, body {
    width: 1200px; height: 768px; overflow: hidden;
    background: var(--backdrop);
    font-family: "Questrial", "Century Gothic", sans-serif;
  }
  .stage {
    position: relative; width: 1200px; height: 768px;
    display: flex; align-items: center; justify-content: center;
  }
  .card {
    position: relative; width: 400px; height: 700px;
    background: var(--card);
    box-shadow: 0 10px 30px rgba(0,0,0,.45);
    overflow: hidden;
  }
  .accent-band {
    position: absolute; left: 0; width: 100%; height: 20px;
    background: linear-gradient(90deg, var(--accent-start), var(--accent-end));
  }
  .accent-band--top { top: 0; }
  .accent-band--bottom { bottom: 0; }

  .doctor { position: absolute; top: 56px; width: 100%; text-align: center; color: var(--ink); }
  .doctor__name { font-size: 30px; font-weight: 400; letter-spacing: 1px; }
  .doctor__creds { font-size: 15px; letter-spacing: 1px; margin-top: 2px; color: var(--ink-soft); }

  .brand {
    position: absolute; top: 150px; width: 100%;
    display: flex; align-items: center; justify-content: center; gap: 12px;
  }
  .brand__dot { width: 34px; height: 34px; border-radius: 50%; background: var(--icon-blue); flex: none; }
  .brand__name { font-size: 33px; line-height: 1.05; color: var(--ink); }
  .tagline {
    position: absolute; top: 252px; width: 100%; text-align: center;
    font-size: 17px; letter-spacing: 3px; color: var(--ink);
  }

  .contact { position: absolute; top: 312px; left: 22px; right: 22px; list-style: none; }
  .contact__row {
    height: 54px; margin-bottom: 10px; background: var(--band);
    display: flex; align-items: center; gap: 12px; padding-left: 16px;
    font-size: 15px; color: var(--ink); letter-spacing: .2px; white-space: nowrap;
  }
  .contact__row--indent { padding-left: 58px; }
  .contact__icon { width: 30px; height: 30px; flex: none; }
</style>
</head>
<body>
<main class="stage">
  <article class="card">
    <div class="accent-band accent-band--top" role="img" aria-label="Colour accent band along the top edge"></div>

    <header class="doctor">
      <h1 class="doctor__name">Darren Wolcott</h1>
      <p class="doctor__creds">DDS, MSD</p>
    </header>

    <div class="brand">
      <span class="brand__dot" aria-hidden="true"></span>
      <p class="brand__name">Brightbay<br>Orthodontics</p>
    </div>
    <p class="tagline">FOR ADULTS &amp; CHILDREN</p>

    <ul class="contact">
      <li class="contact__row">
        <svg class="contact__icon" viewBox="0 0 30 30" aria-hidden="true">
          <path d="M4 11c0-4 22-4 22 0v3h-6v-3H10v3H4z" fill="var(--icon-blue)"/>
          <path d="M9 14h12l4 10H5z" fill="var(--icon-blue)"/>
          <circle cx="15" cy="19" r="3" fill="var(--card)"/>
        </svg>
        555-418-2637
      </li>
      <li class="contact__row">
        <svg class="contact__icon" viewBox="0 0 30 30" aria-hidden="true">
          <circle cx="15" cy="15" r="12" fill="none" stroke="var(--icon-blue)" stroke-width="3"/>
          <circle cx="15" cy="15" r="7" fill="var(--icon-blue)"/>
        </svg>
        www.brightbayortho.example
      </li>
      <li class="contact__row">
        <svg class="contact__icon" viewBox="0 0 30 30" aria-hidden="true">
          <rect x="2" y="7" width="26" height="17" fill="var(--icon-blue)"/>
          <path d="M2 7l13 10L28 7" fill="none" stroke="var(--card)" stroke-width="2"/>
        </svg>
        info@brightbayortho.example
      </li>
      <li class="contact__row">
        <svg class="contact__icon" viewBox="0 0 30 30" aria-hidden="true">
          <path d="M15 2a9 9 0 0 1 9 9c0 7-9 17-9 17S6 18 6 11a9 9 0 0 1 9-9z" fill="var(--icon-blue)"/>
          <circle cx="15" cy="11" r="3.5" fill="var(--card)"/>
        </svg>
        5214 West Linden Avenue, Suite 204
      </li>
      <li class="contact__row contact__row--indent">Ridgeford, OR 76991</li>
    </ul>

    <div class="accent-band accent-band--bottom" role="img" aria-label="Colour accent band along the bottom edge"></div>
  </article>
</main>
</body>
</html>
```